Irrigation Business needs their business cards modernised and revamped

I would like to keep my current logo, colours and revamp the format of the card.

I would like the card to be clean yet important.

Im not sure if you include texture but i would like the named logo to be indented into the card etc.

show me something alive and free something thats clinical to the point yet has a feel of achievement. i would like people to go nice card.

Target Market(s)

high end clients, corporate, sports field manger, the guys that make the decisions

Industry/Entity Type

Business

Contact Information for Business Card

nformation to be included

Dean Harlow (Director)
0487305526
dean@kolvat.biz
www.kestonfieldworks.com

instagram logo
google logo
facebook logo

Colors

Designer to choose colors to be used in the design.

Requirements
Nice to have
• indentations a really nice feel to the card good texture

```html
<!DOCTYPE html>
<html lang="en">
<head>
<meta charset="utf-8">
<title>Keston Fieldworks – Business Card</title>
<link rel="stylesheet" href="https://fonts.googleapis.com/css2?family=Roboto+Condensed:wght@400;700&family=Roboto:wght@400;700;900&display=swap">
<style>
  :root {
    --backdrop: #2b2b2b;
    --card-white: #f4f4f4;
    --brand-navy: #2b5ea8;
    --brand-sky: #35a7d8;
    --brand-sky-deep: #2a9fd3;
    --brand-green: #2fa04a;
    --rule-grey: #cfcfcf;
    --text-white: #ffffff;
  }
  * { box-sizing: border-box; margin: 0; padding: 0; }
  html, body { width: 1200px; height: 886px; overflow: hidden; }
  body {
    background: var(--backdrop);
    position: relative;
    font-family: "Roboto", Arial, sans-serif;
  }
  .card {
    position: absolute;
    width: 540px;
    height: 310px;
    border-radius: 22px;
    overflow: hidden;
    box-shadow: 0 10px 28px rgba(0,0,0,.45);
  }
  /* Front: brand side */
  .card-front {
    left: 80px; top: 120px;
    background: var(--card-white);
  }
  .brand {
    position: absolute;
    top: 78px; left: 0; right: 0;
    display: flex; flex-direction: column; align-items: center;
  }
  .brand-dot {
    width: 78px; height: 78px; border-radius: 50%;
    background: var(--brand-sky);
    margin-bottom: 18px;
  }
  .brand-name {
    font-family: "Roboto", Arial, sans-serif;
    font-weight: 900;
    font-size: 34px;
    letter-spacing: -0.5px;
    color: var(--brand-navy);
    text-transform: uppercase;
  }
  .divider {
    position: absolute;
    left: 40px; right: 40px; top: 250px;
    height: 1px; background: var(--rule-grey);
  }
  .social {
    position: absolute;
    top: 237px; left: 50%;
    transform: translateX(-50%);
    display: flex; gap: 8px;
    padding: 0 10px;
    background: var(--card-white);
  }
  .social-dot {
    width: 26px; height: 26px; border-radius: 50%;
    background: var(--brand-navy);
  }
  /* Back: contact side */
  .card-back {
    left: 580px; top: 456px;
    background: linear-gradient(160deg, var(--brand-sky) 0%, var(--brand-sky-deep) 100%);
  }
  .stripes {
    position: absolute; right: 0; top: 0;
    width: 118px; height: 100%;
  }
  .contact {
    position: absolute;
    left: 60px; top: 0; bottom: 0;
    display: flex; align-items: center; gap: 34px;
  }
  .mark {
    width: 62px; height: 62px; border-radius: 50%;
    background: var(--text-white);
    flex: none;
  }
  .details { color: var(--text-white); }
  .person-name {
    font-family: "Roboto Condensed", Arial, sans-serif;
    font-weight: 700; font-size: 30px;
    text-transform: uppercase; line-height: 1;
  }
  .person-role {
    font-family: "Roboto Condensed", Arial, sans-serif;
    font-size: 15px; letter-spacing: 1px;
    text-transform: uppercase; margin-top: 6px;
  }
  .dash {
    width: 16px; height: 2px; background: var(--text-white);
    margin: 14px 0;
  }
  .contact-line {
    font-family: "Roboto Condensed", Arial, sans-serif;
    font-size: 15px; line-height: 1.45;
  }
</style>
</head>
<body>
  <section class="card card-front" aria-label="Card front">
    <div class="brand">
      <div class="brand-dot"></div>
      <div class="brand-name">Keston Fieldworks</div>
    </div>
    <div class="divider"></div>
    <div class="social" aria-label="Social links">
      <span class="social-dot"></span>
      <span class="social-dot"></span>
      <span class="social-dot"></span>
    </div>
  </section>

  <section class="card card-back" aria-label="Card back">
    <div class="contact">
      <div class="mark"></div>
      <div class="details">
        <div class="person-name">Dean Harlow</div>
        <div class="person-role">Director</div>
        <div class="dash"></div>
        <div class="contact-line">0487305526</div>
        <div class="contact-line">dean@kolvat.biz</div>
        <div class="contact-line">www.kestonfieldworks.com</div>
      </div>
    </div>
    <svg class="stripes" viewBox="0 0 118 310" preserveAspectRatio="none" aria-hidden="true">
      <rect x="0" y="0" width="118" height="310" fill="#ffffff"/>
      <rect x="6" y="0" width="20" height="310" fill="#2b5ea8"/>
      <rect x="32" y="0" width="20" height="310" fill="#2b5ea8"/>
      <rect x="58" y="0" width="20" height="310" fill="#2b5ea8"/>
      <rect x="84" y="0" width="34" height="310" fill="#2b5ea8"/>
    </svg>
  </section>
</body>
</html>
```